Marrowby Water Taxi and Transport Business Card

I need business cards for my new water taxi and freight transport business I have started here in Kodiak Alaska. Kodiak is a remote island in the middle of the gulf of Alaska. There are seven native villages around the island and Kodiak is the #2 fishing port in the United States. We also have the largest Coast Guard Base in the U.S. My company will be providing water taxi and freight transport logistics to the villages and many hunting and fishing lodges as well as remote properties around the island.

I would like a business card that isn't status quo, something that stands out, either in feel or appearance. I do like clean minimal designs but it needs to have the necessary contact info on it.

Target Market(s)

remote lodge / property owners, residents of the many villages around Kodiak and any one wanting to enjoy the great outdoors of Kodiak Alaska

Industry/Entity Type

Business

Contact Information for Business Card

I like clean simple designs that aren't cluttered but still provide the necessary information

Colors
0255a3
3277b5
33a4d5
9bcb3c
add136
fbed22
ffc214
f78f20
f37122

Requirements
Must have
• logo and contact info
• Captain Mason Elwick
• www.marrowbyferryline.com
• mason@marrowbyferryline.com

```html
<!DOCTYPE html>
<html lang="en">
<head>
<meta charset="utf-8">
<title>Marrowby Water Taxi and Transport – Business Card</title>
<link href="https://fonts.googleapis.com/css2?family=Questrial&display=swap" rel="stylesheet">
<style>
  :root {
    --backdrop: #e8e5e1;
    --card-frost: #f4f5f6;
    --card-frost-edge: #e3e6ea;
    --navy-deep: #0a2766;
    --navy: #1d4b9f;
    --sky: #33a4d5;
    --orange: #f37122;
    --brand-ink: #1f3e72;
    --text-light: #e4e9f3;
    --name-silver: #c9ccd2;
  }
  * { margin: 0; padding: 0; box-sizing: border-box; }
  html, body {
    width: 1200px; height: 969px; overflow: hidden;
    background: var(--backdrop);
    font-family: "Questrial", "Century Gothic", sans-serif;
  }
  .canvas { position: relative; width: 1200px; height: 969px; }
  .business-card {
    position: absolute; left: 100px; top: 201px;
    width: 1000px; height: 567px;
    border-radius: 34px; overflow: hidden;
    background: linear-gradient(180deg, var(--card-frost), var(--card-frost-edge));
    box-shadow: 0 18px 40px rgba(0,0,0,0.18);
  }
  .card-waves { position: absolute; inset: 0; width: 100%; height: 100%; }
  .brand-name {
    position: absolute; right: 80px; top: 160px;
    display: flex; align-items: center; gap: 18px;
    color: var(--brand-ink);
  }
  .brand-dot { width: 46px; height: 46px; border-radius: 50%; background: var(--orange); }
  .brand-text { display: flex; flex-direction: column; line-height: 1; }
  .brand-text .word { font-size: 62px; letter-spacing: 1px; }
  .brand-text .tagline { font-size: 27px; margin-top: 8px; }
  .contact-block {
    position: absolute; left: 46px; top: 340px;
    color: var(--text-light); font-size: 25px; line-height: 1.25;
  }
  .address { margin-bottom: 18px; }
  .contact-line { display: flex; align-items: center; gap: 14px; height: 38px; }
  .contact-line svg { width: 22px; height: 22px; flex: none; }
  .person {
    position: absolute; right: 62px; top: 412px; text-align: right;
  }
  .person-name { color: var(--name-silver); font-size: 35px; letter-spacing: 1px; }
  .person-title { color: var(--text-light); font-size: 27px; margin-top: 6px; }
</style>
</head>
<body>
<main class="canvas">
  <section class="business-card">
    <svg class="card-waves" viewBox="0 0 1000 567" preserveAspectRatio="none" aria-hidden="true">
      <defs>
        <linearGradient id="navyBody" x1="0" y1="0" x2="0.3" y2="1">
          <stop offset="0" stop-color="#2556ab"/>
          <stop offset="1" stop-color="#0a2766"/>
        </linearGradient>
      </defs>
      <path d="M0 300 C 80 280, 160 265, 260 268 C 360 272, 440 285, 520 302 C 420 292, 300 287, 200 294 C 120 300, 60 310, 0 320 Z" fill="var(--orange)"/>
      <path d="M150 302 C 300 272, 480 292, 640 326 C 780 352, 900 322, 1000 286 L1000 302 C 900 337, 780 362, 640 340 C 480 312, 300 292, 150 308 Z" fill="var(--sky)"/>
      <path d="M0 320 C 150 298, 330 292, 500 318 C 640 342, 800 356, 1000 302 L1000 567 L0 567 Z" fill="url(#navyBody)"/>
    </svg>

    <div class="brand-name">
      <span class="brand-dot"></span>
      <div class="brand-text">
        <span class="word">MARROWBY</span>
        <span class="tagline">Water Taxi and Transport</span>
      </div>
    </div>

    <div class="contact-block">
      <p class="address">4120 Harborview Road<br>Anchorage, Alaska 99515</p>
      <p class="contact-line">
        <svg viewBox="0 0 24 24"><path fill="#e4e9f3" d="M6.6 2.5l3 3.2-1.8 2.6c1.3 2.8 3.4 4.9 6.2 6.2l2.6-1.8 3.2 3-1.6 3.6C10.8 19.6 4.4 13.2 3 5.4z"/></svg>
        907 555 0148
      </p>
      <p class="contact-line">
        <svg viewBox="0 0 24 24"><rect x="2" y="5" width="20" height="14" rx="1.5" fill="#e4e9f3"/><path d="M2.5 6l9.5 7 9.5-7" fill="none" stroke="#1d4b9f" stroke-width="1.6"/></svg>
        mason@marrowbyferryline.com
      </p>
      <p class="contact-line">
        <svg viewBox="0 0 24 24"><circle cx="12" cy="12" r="10" fill="#e4e9f3"/><path d="M2 12h20M12 2c3 3 3 17 0 20M12 2c-3 3-3 17 0 20" fill="none" stroke="#1d4b9f" stroke-width="1.4"/></svg>
        www.marrowbyferryline.com
      </p>
    </div>

    <div class="person">
      <p class="person-name">MASON ELWICK</p>
      <p class="person-title">Captain</p>
    </div>
  </section>
</main>
</body>
</html>
```